National appliance rental company needs a newspaper ad design

We need an ad template that we can use for different newspaper advertising. Ad is to be colourful - I have attached our current marketing so you have an idea of colours.
Text to be something like the below:

Want it, Rent it, Own it!

Need to update your furniture? Kids need stuff for school?

(Put in pics of phones and TV)

Zelvos starting from just $8 per week
Smart phones starting from $10 per week
Large family fridges from $30 per week

TV’s, laptops, whitegoods, furniture, beds – we will finance just about anything!

Fast approvals – call 1300 582 967 or go to www.brightwellhomeleasing.com.au/apply - NOW!
$50 credit voucher given to the first 10 successful applicants.

(Pic of logo somewhere)
Terms and conditions apply. Pricing based on 24 month term

Brightwell Home Leasing P/L ACN 061 847 293. Australian Credit Licence # 718294

Target Market(s)

Low income people and families

Industry/Entity Type

Appliance

Requirements
Must have
• I would love to have a couple of different sizes.
• Maybe 6cm x 10 cm, and also 10cms x 10cms.
Nice to have
• Please use the green from fridge magnet and colours from our logo, etc.

```html
<!DOCTYPE html>
<html lang="en">
<head>
<meta charset="utf-8">
<title>Brightwell Home Leasing – Newspaper Ad</title>
<link href="https://fonts.googleapis.com/css2?family=Arimo:ital,wght@0,400;0,700;1,400&family=Lilita+One&display=swap" rel="stylesheet">
<style>
  :root {
    --page-bg: #e6e2dc;
    --ad-white: #ffffff;
    --ad-grey: #e9e9e9;
    --brand-red: #e0262b;
    --brand-blue: #1a6fb3;
    --brand-green: #6cb33f;
    --brand-yellow: #f7c400;
    --price-yellow: #ffd400;
    --ink: #1e1e1e;
    --white: #ffffff;
  }
  * { box-sizing: border-box; margin: 0; padding: 0; }
  html, body { width: 1200px; height: 1000px; overflow: hidden; }
  body { background: var(--page-bg); font-family: "Arimo", Arial, sans-serif; position: relative; }

  .ad {
    position: absolute; left: 318px; top: 12px; width: 580px; height: 966px;
    background: linear-gradient(to bottom, var(--ad-white) 0%, var(--ad-grey) 45%, var(--ad-white) 70%);
    overflow: hidden;
  }
  .mascot-art {
    position: absolute; left: 97px; top: 8px; width: 120px; height: 172px;
    background: linear-gradient(135deg, #f4f4f4, #bdbdbd); border-radius: 14px;
  }
  .brand-name {
    position: absolute; left: 225px; top: 58px; width: 270px;
    font-weight: 700; font-size: 40px; line-height: 44px; color: var(--brand-red);
    white-space: nowrap;
  }
  .brand-tagline {
    position: absolute; left: 225px; top: 156px; width: 270px;
    font-style: italic; font-size: 15px; line-height: 18px; color: var(--ink); text-align: center;
  }
  .headline { position: absolute; left: 0; top: 190px; width: 580px; height: 110px; }
  .headline text {
    font-family: "Lilita One", "Arial Black", sans-serif; font-size: 50px;
    fill: var(--brand-red); stroke: var(--white); stroke-width: 6px; paint-order: stroke;
  }
  .subhead {
    position: absolute; left: 60px; top: 262px; width: 460px; text-align: center;
    font-weight: 700; font-size: 20px; line-height: 25px; color: var(--ink);
  }
  .phones-art {
    position: absolute; left: 42px; top: 316px; width: 215px; height: 140px;
    background: linear-gradient(135deg, #d8e6f2, #2a2a2a 55%, #2f9bd6); border-radius: 12px;
  }
  .tv-art {
    position: absolute; left: 40px; top: 445px; width: 188px; height: 185px;
    background: linear-gradient(160deg, #3a3a3a, #0c0c0c); border-radius: 6px;
  }
  .price-panel {
    position: absolute; left: 270px; top: 323px; width: 310px; height: 230px;
    background: var(--brand-blue); border-radius: 14px 0 0 14px;
    color: var(--white); font-size: 24px; line-height: 27px; padding: 12px 0 0 20px;
    white-space: nowrap;
  }
  .price-panel li { list-style: none; padding-left: 18px; text-indent: -18px; margin-bottom: 18px; }
  .price-panel li::before { content: "• "; }
  .price-panel strong { color: var(--price-yellow); font-weight: 700; }
  .voucher {
    position: absolute; left: 354px; top: 548px; width: 224px; height: 224px;
    background: var(--brand-yellow); border: 4px solid var(--white); border-radius: 50%;
    color: var(--brand-red); font-weight: 700; font-size: 23px; line-height: 28px;
    padding-top: 38px; text-align: center; white-space: nowrap;
  }
  .finance-panel {
    position: absolute; left: 12px; top: 642px; width: 380px; height: 125px;
    background: var(--brand-blue); border-radius: 12px; color: var(--white);
    font-size: 24px; line-height: 28px; text-align: center; padding: 8px 50px 0 6px;
    white-space: nowrap;
  }
  .apply-band {
    position: absolute; left: 0; top: 775px; width: 580px; height: 108px;
    background: var(--white); padding: 3px;
  }
  .apply-band__inner {
    background: var(--brand-green); width: 100%; height: 100%; text-align: center;
    color: var(--ink); padding-top: 8px;
  }
  .apply-band__title {
    font-weight: 700; font-size: 30px; line-height: 32px; color: var(--brand-red);
  }
  .apply-band__call { font-size: 23px; line-height: 28px; }
  .apply-band__web { font-size: 22px; line-height: 28px; }
  .apply-band b { font-weight: 700; }
  .legal-band {
    position: absolute; left: 0; top: 886px; width: 580px; height: 80px;
    background: var(--brand-red); color: var(--white); text-align: center;
    font-weight: 700; font-size: 17px; line-height: 21px; padding-top: 5px;
  }
</style>
</head>
<body>
  <main class="ad">
    <div class="mascot-art" role="img" aria-label="Cartoon fridge mascot illustration"></div>
    <div class="brand-name">Brightwell<br>Home Leasing</div>
    <div class="brand-tagline">“It’s cheaper to lease smart!”</div>

    <svg class="headline" viewBox="0 0 580 110" aria-label="Want it, Rent it, Own it!">
      <defs><path id="headline-arc" d="M20 80 Q290 20 560 95"/></defs>
      <text><textPath href="#headline-arc" startOffset="50%" text-anchor="middle">Want it, Rent it, Own it!</textPath></text>
    </svg>

    <p class="subhead">Need to update your furniture?<br>Kids need stuff for school?</p>

    <div class="phones-art" role="img" aria-label="Photo of three smartphones"></div>
    <div class="tv-art" role="img" aria-label="Photo of a flat screen television"></div>

    <ul class="price-panel">
      <li>Zelvos starting from<br>just <strong>$8</strong> per week</li>
      <li>Smart phones starting<br>from <strong>$10</strong> per week</li>
      <li>Large family fridges<br>from <strong>$30</strong> per week</li>
    </ul>

    <div class="finance-panel">TV’s, laptops, whitegoods,<br>furniture, beds –<br>we will finance just<br>about anything!</div>

    <div class="voucher">$50 credit<br>voucher given<br>to the first<br>10 successful<br>applicants.</div>

    <section class="apply-band">
      <div class="apply-band__inner">
        <div class="apply-band__title">FAST APPROVALS</div>
        <div class="apply-band__call">call <b>1300 582 967</b> or go to</div>
        <div class="apply-band__web">www.brightwellhomeleasing.com.au/apply - <b>NOW!</b></div>
      </div>
    </section>

    <footer class="legal-band">
      Terms and conditions apply. Pricing based on 24 month term<br>
      Brightwell Home Leasing P/L ACN 061 847 293.<br>
      Australian Credit Licence # 718294
    </footer>
  </main>
</body>
</html>
```